Silas Merton Moving DL Flyer

We need a double sided DL flyer to give to patients to let them know that we are moving location.
On one side we would like it to read:
"We Are Moving!" and "November 2017" and our logo.
On the other side we would like it to read:
"Same Great Staff"
"Same Great Service"
"Bigger, Brighter and Better"
"New Location at 59 Quarry Ln"
with a map below (attached)
The flyer should follow our practice branding. Attached is a copy of our business card as an example of this.

```html
<!DOCTYPE html>
<html lang="en">
<head>
<meta charset="utf-8">
<title>Silas Merton Optometry – Moving Flyer</title>
<link href="https://fonts.googleapis.com/css2?family=Oswald:wght@300;700&family=Roboto+Condensed:wght@400;700&family=Open+Sans:wght@400&display=swap" rel="stylesheet">
<style>
  :root {
    --plum: #4a3a53;
    --plum-dark: #3b2e43;
    --ink: #2b2430;
    --paper: #ffffff;
    --backdrop: #e8e7ea;
    --photo-light: #eceaea;
    --photo-mid: #c9c4c2;
    --map-grey: #c4c4c4;
    --map-dark: #a9a9ab;
  }
  * { box-sizing: border-box; margin: 0; padding: 0; }
  html, body { width: 1200px; height: 1169px; overflow: hidden; }
  body { background: var(--backdrop); position: relative; font-family: "Open Sans", sans-serif; color: var(--ink); }

  .flyer {
    position: absolute; left: 125px; width: 951px; height: 474px;
    background: var(--paper); overflow: hidden;
    box-shadow: 0 6px 18px rgba(0,0,0,.18);
  }
  .flyer--front { top: 81px; }
  .flyer--back { top: 614px; }

  .brand { position: absolute; left: 62px; top: 42px; display: flex; align-items: flex-start; gap: 14px; }
  .brand__square { width: 18px; height: 18px; background: var(--plum); margin-top: 10px; }
  .brand__name { font-family: "Roboto Condensed", sans-serif; font-weight: 400; color: var(--plum-dark); font-size: 40px; line-height: 1.02; }
  .brand__tagline { position: absolute; left: 94px; top: 140px; font-family: "Open Sans", sans-serif; font-size: 17px; color: var(--plum); }

  /* Front */
  .front__lead { position: absolute; left: 0; width: 436px; top: 186px; text-align: center; font-family: "Oswald", sans-serif; font-weight: 300; font-size: 44px; color: var(--plum); letter-spacing: 1px; }
  .front__rule { position: absolute; left: 104px; width: 228px; top: 244px; height: 2px; background: var(--plum); }
  .front__headline { position: absolute; left: 0; width: 436px; top: 236px; text-align: center; font-family: "Oswald", sans-serif; font-weight: 700; font-size: 96px; line-height: 1.1; color: var(--plum); }
  .front__date { position: absolute; left: 0; width: 436px; top: 344px; text-align: center; font-family: "Roboto Condensed", sans-serif; font-weight: 700; font-size: 29px; color: var(--ink); }
  .front__web { position: absolute; left: 43px; top: 396px; width: 346px; height: 46px; border-radius: 6px; background: var(--plum); color: #fff; font-family: "Roboto Condensed", sans-serif; font-weight: 700; font-size: 25px; line-height: 46px; text-align: center; box-shadow: 0 5px 8px rgba(0,0,0,.25); }

  .art { position: absolute; top: 0; right: 0; height: 474px; }
  .art--photo { width: 400px; }
  .art--map { width: 370px; }

  /* Back */
  .back__headline { position: absolute; left: 0; width: 436px; top: 198px; text-align: center; font-family: "Roboto Condensed", sans-serif; font-weight: 700; font-size: 46px; color: var(--plum); }
  .back__sub { position: absolute; left: 0; width: 436px; top: 257px; text-align: center; font-family: "Roboto Condensed", sans-serif; font-weight: 700; font-size: 29px; color: var(--plum); }
  .back__banner { position: absolute; left: 34px; top: 302px; width: 366px; height: 40px; background: var(--plum); color: #fff; text-align: center; line-height: 40px; font-family: "Roboto Condensed", sans-serif; font-weight: 700; font-size: 23px; box-shadow: 0 4px 6px rgba(0,0,0,.2); }

  .contact { position: absolute; left: 28px; top: 390px; width: 206px; list-style: none; }
  .contact__item { display: flex; align-items: center; gap: 8px; font-size: 12.5px; height: 25px; color: var(--ink); white-space: nowrap; }
  .contact__icon { width: 13px; height: 13px; flex: none; }
  .contact__divider { position: absolute; left: 242px; top: 386px; width: 2px; height: 80px; background: var(--plum); }
  .call { position: absolute; left: 256px; top: 386px; }
  .call__label { font-family: "Roboto Condensed", sans-serif; font-weight: 700; font-size: 20px; color: var(--plum); }
  .call__number { font-family: "Roboto Condensed", sans-serif; font-weight: 700; font-size: 40px; line-height: 1; color: var(--plum); }
</style>
</head>
<body>

<section class="flyer flyer--front">
  <div class="brand">
    <span class="brand__square"></span>
    <div class="brand__name">Silas Merton<br>Optometry</div>
  </div>
  <p class="brand__tagline">See Better. See Us.</p>

  <p class="front__lead">WE ARE</p>
  <div class="front__rule"></div>
  <h1 class="front__headline">MOVING</h1>
  <p class="front__date">NOVEMBER 2017</p>
  <div class="front__web">www.silasmerton.com.au</div>

  <svg class="art art--photo" viewBox="0 0 400 474" role="img" aria-label="Photo of an optometrist fitting trial frames on a smiling young patient">
    <defs>
      <linearGradient id="photoTone" x1="0" y1="0" x2="1" y2="1">
        <stop offset="0" stop-color="var(--photo-light)"/>
        <stop offset="1" stop-color="var(--photo-mid)"/>
      </linearGradient>
    </defs>
    <path d="M70 0 H400 V474 H0 C40 330 60 170 70 0 Z" fill="url(#photoTone)"/>
    <path d="M70 0 C60 170 40 330 0 474" fill="none" stroke="var(--plum)" stroke-width="6"/>
  </svg>
</section>

<section class="flyer flyer--back">
  <div class="brand">
    <span class="brand__square"></span>
    <div class="brand__name">Silas Merton<br>Optometry</div>
  </div>
  <p class="brand__tagline">See Better. See Us.</p>

  <h2 class="back__headline">Same Great Staff</h2>
  <p class="back__sub">Same Great Service</p>
  <div class="back__banner">BIGGER, BRIGHTER AND BETTER</div>

  <ul class="contact">
    <li class="contact__item">
      <svg class="contact__icon" viewBox="0 0 16 16"><circle cx="8" cy="8" r="7.5" fill="var(--plum)"/><path d="M8 3.5a3 3 0 0 1 3 3c0 2.2-3 6-3 6s-3-3.8-3-6a3 3 0 0 1 3-3z" fill="#fff"/><circle cx="8" cy="6.5" r="1" fill="var(--plum)"/></svg>
      New Location at 59 Quarry Ln
    </li>
    <li class="contact__item">
      <svg class="contact__icon" viewBox="0 0 16 16"><circle cx="8" cy="8" r="7.5" fill="var(--plum)"/><rect x="4" y="5.5" width="8" height="5.5" fill="#fff"/><path d="M4 5.5 8 8.6 12 5.5" fill="none" stroke="var(--plum)" stroke-width="1"/></svg>
      silas@silasmerton.com.au
    </li>
    <li class="contact__item">
      <svg class="contact__icon" viewBox="0 0 16 16"><circle cx="8" cy="8" r="7.5" fill="var(--plum)"/><circle cx="8" cy="8" r="4" fill="none" stroke="#fff" stroke-width="1.2"/><path d="M4 8h8M8 4c-1.6 2.4-1.6 5.6 0 8M8 4c1.6 2.4 1.6 5.6 0 8" fill="none" stroke="#fff" stroke-width="0.9"/></svg>
      www.silasmerton.com.au
    </li>
  </ul>
  <div class="contact__divider"></div>
  <div class="call">
    <p class="call__label">CALL NOW</p>
    <p class="call__number">6541 2870</p>
  </div>

  <svg class="art art--map" viewBox="0 0 370 474" role="img" aria-label="Street map showing the new practice location and surrounding streets">
    <defs>
      <linearGradient id="mapTone" x1="0" y1="0" x2="1" y2="1">
        <stop offset="0" stop-color="var(--map-grey)"/>
        <stop offset="1" stop-color="var(--map-dark)"/>
      </linearGradient>
    </defs>
    <path d="M60 0 H370 V474 H0 C30 330 50 170 60 0 Z" fill="url(#mapTone)"/>
    <path d="M60 0 C50 170 30 330 0 474" fill="none" stroke="var(--plum)" stroke-width="6"/>
  </svg>
</section>

</body>
</html>
```